Business card design Needed for new logo / Construction business, home extensions and new builds

We need a business card design using our new logo files which i will attach to this project :)

We are a small construction business specialising in home extensions, new builds and property development. We are very ambitious and would appreciate professional and elegant designs for our new business card.

Very serious about using the services on MakerQuarry and recently acquired our new logo from here :)

Please get involved, i will feedback when i can as i am very busy but can respond daily, thanks

Target Market(s)

People that want to build onto their houses, new building developments or adding too their existing property

Industry/Entity Type

Construction

Contact Information for Business Card

Renwick Tolliver Construction, Lionel Ashby (Managing Director), Tel 07822254961, email - info@renwick-tolliver, www.renwick-tolliver.co.uk

Colors

Designer to choose colors to be used in the design.

Requirements
Must have
• I like a deep grey on the back please. A lot of you have provided black from and back, try mixing things up a little. The black looks cool 😎 Thanks

```html
<!DOCTYPE html>
<html lang="en">
<head>
<meta charset="utf-8">
<title>Renwick Tolliver Construction – Business Card</title>
<link rel="stylesheet" href="https://fonts.googleapis.com/css2?family=Open+Sans:wght@400;600;700&display=swap">
<style>
  :root {
    --stage: #222223;
    --card-black: #1d1d20;
    --deep-grey: #2b2b2e;
    --deep-grey-light: #3a3a3e;
    --gold: #d9a232;
    --gold-light: #f6d98c;
    --gold-dark: #b07a1c;
    --silver: #c9c9cc;
    --silver-dark: #8e8f93;
    --white: #ffffff;
  }
  * { box-sizing: border-box; margin: 0; padding: 0; }
  html, body {
    width: 1200px; height: 780px; overflow: hidden;
    background: var(--stage);
    font-family: "Open Sans", Arial, sans-serif;
  }
  .canvas {
    width: 1200px; height: 780px;
    display: flex; flex-direction: column; align-items: center; justify-content: center;
    gap: 28px;
  }
  .card {
    position: relative;
    width: 620px; height: 354px;
    border-radius: 3px;
    overflow: hidden;
    box-shadow: 0 14px 30px rgba(0,0,0,.55);
  }

  /* Back */
  .card-back {
    background: radial-gradient(ellipse at 75% 10%, var(--deep-grey-light), var(--deep-grey) 55%, #252528 100%);
  }
  .card-back .pattern-area { position: absolute; inset: 0; }
  .card-back .back-brand {
    position: absolute; right: 26px; bottom: 22px;
    display: flex; align-items: center; gap: 6px;
    font-size: 9px; font-weight: 600; letter-spacing: .06em;
    color: var(--gold); text-transform: uppercase;
  }
  .brand-square { width: 8px; height: 8px; background: var(--gold); }

  /* Front */
  .card-front { background: var(--card-black); }
  .card-front .band { position: absolute; inset: 0; }
  .brand {
    position: absolute; left: 0; right: 0; top: 40px;
    display: flex; flex-direction: column; align-items: center; gap: 10px;
  }
  .brand-square-lg { width: 26px; height: 26px; background: var(--gold); }
  .brand-name {
    font-size: 17px; font-weight: 600; letter-spacing: .12em;
    color: var(--silver); text-transform: uppercase; text-align: center;
  }
  .person {
    position: absolute; left: 62px; top: 142px;
    text-align: right; width: 214px;
  }
  .person-name { font-size: 30px; font-weight: 700; line-height: 1.1; }
  .person-name .first { color: var(--silver); }
  .person-name .last { color: var(--gold); }
  .person-role { font-size: 14px; color: var(--white); margin-top: 2px; }
  .divider {
    position: absolute; left: 298px; top: 142px;
    width: 2px; height: 62px; background: var(--white);
  }
  .contacts {
    position: absolute; left: 320px; top: 140px;
    list-style: none; display: flex; flex-direction: column; gap: 4px;
    font-size: 13px; line-height: 18px; color: var(--white);
  }
  .contacts li { display: flex; align-items: center; gap: 8px; }
  .contacts svg { width: 13px; height: 13px; flex: none; }
  .address {
    position: absolute; right: 40px; bottom: 26px;
    font-size: 14px; font-weight: 600; color: var(--white);
    letter-spacing: .02em;
  }
</style>
</head>
<body>
<main class="canvas">

  <section class="card card-back" aria-label="Card back">
    <div class="pattern-area" role="img" aria-label="Repeating tone-on-tone monogram pattern across the deep grey back"></div>
    <div class="back-brand"><span class="brand-square"></span>Renwick Tolliver</div>
  </section>

  <section class="card card-front" aria-label="Card front">
    <svg class="band" viewBox="0 0 620 354" preserveAspectRatio="none" aria-hidden="true">
      <defs>
        <linearGradient id="goldBand" x1="0" y1="0" x2="0" y2="1">
          <stop offset="0" stop-color="#e3b04a"/>
          <stop offset=".35" stop-color="#f6d98c"/>
          <stop offset=".7" stop-color="#d9a232"/>
          <stop offset="1" stop-color="#b07a1c"/>
        </linearGradient>
        <linearGradient id="silverLine" x1="0" y1="0" x2="1" y2="0">
          <stop offset="0" stop-color="#8e8f93" stop-opacity="0"/>
          <stop offset=".3" stop-color="#8e8f93"/>
          <stop offset=".75" stop-color="#e6e6e8"/>
          <stop offset="1" stop-color="#c9c9cc"/>
        </linearGradient>
      </defs>
      <path d="M0 292 C 250 287, 470 256, 620 210 L620 354 L0 354 Z" fill="url(#goldBand)"/>
      <path d="M24 284 C 250 279, 470 248, 612 203" fill="none" stroke="url(#silverLine)" stroke-width="3"/>
    </svg>

    <div class="brand">
      <span class="brand-square-lg"></span>
      <div class="brand-name">Renwick Tolliver Construction</div>
    </div>

    <div class="person">
      <div class="person-name"><span class="first">Lionel</span> <span class="last">Ashby</span></div>
      <div class="person-role">Managing Director</div>
    </div>

    <div class="divider"></div>

    <ul class="contacts">
      <li>
        <svg viewBox="0 0 16 16" aria-hidden="true"><path fill="#d9a232" d="M3.5 1.5l2.5 3-1.5 1.5c.8 2 2.5 3.7 4.5 4.5l1.5-1.5 3 2.5-1.8 2.2C6.5 13.5 2.5 9.5 1.3 3.3z"/></svg>
        0782 225 4961
      </li>
      <li>
        <svg viewBox="0 0 16 16" aria-hidden="true"><circle cx="8" cy="8" r="6.5" fill="none" stroke="#d9a232" stroke-width="1.5"/><path d="M1.5 8h13M8 1.5c-3 3.5-3 9.5 0 13M8 1.5c3 3.5 3 9.5 0 13" fill="none" stroke="#d9a232" stroke-width="1.2"/></svg>
        info@renwick-tolliver.co.uk
      </li>
      <li>
        <svg viewBox="0 0 16 16" aria-hidden="true"><rect x="1.5" y="3.5" width="13" height="9" fill="none" stroke="#d9a232" stroke-width="1.5"/><path d="M1.5 3.5l6.5 5 6.5-5" fill="none" stroke="#d9a232" stroke-width="1.3"/></svg>
        www.renwick-tolliver.co.uk
      </li>
    </ul>

    <div class="address">Hollin Lane, Ashcombe Westbury, WB4 7QE</div>
  </section>

</main>
</body>
</html>
```